Webdesign für Hersteller für Pack- und Palettieranlagen für den Getränke- und Lebensmittelbereich
Webdesign für Hersteller für Pack- und Palettieranlagen für den Getränke- und Lebensmittelbere..
Zielgruppe
Hersteller für Pack- und Palettieranlagen für den Getränke- und Lebensmittelbereich
Zielgruppe: Getränke- und Lebensmittelhersteller
Aufgabenstellung
die zukünftige Seite soll dynamischer und intuitiver werden
klare Strukturen, aber morderner als das jetztige Layout
Keine Kopie der alten Seite www.kolmatech.de!
Startseite soll aufgeräumter sein
Logo, Rufnummer, Mail, Social Media
Startseite mit großem Headerbild (Slider)

```html
<!DOCTYPE html>
<html lang="de">
<head>
<meta charset="utf-8">
<title>KOLMATECH Maschinenbau GmbH</title>
<link href="https://fonts.googleapis.com/css2?family=Hanken+Grotesk:wght@300;400;500;600;700&display=swap" rel="stylesheet">
<style>
:root{
  --green:#6db33f;
  --green-dark:#4e9a26;
  --gray-bg:#f5f5f5;
  --text:#222;
  --muted:#555;
  --white:#fff;
}
*{margin:0;padding:0;box-sizing:border-box}
html,body{width:1200px;height:3419px;overflow:hidden}
body{font-family:"Hanken Grotesk",sans-serif;color:var(--text);background:var(--gray-bg);position:relative}
.abs{position:absolute}
.btn{position:absolute;display:flex;align-items:center;justify-content:center;font-weight:600;font-size:13px;border-radius:2px}
.btn-fill{background:var(--green);color:var(--white)}
.btn-line{border:1.5px solid var(--green);color:var(--green);background:var(--white)}
.section-title{position:absolute;left:0;width:1200px;text-align:center;color:var(--green);font-weight:600;font-size:42px;letter-spacing:-.5px}
.section-sub{position:absolute;left:0;width:1200px;text-align:center;font-size:15px}
.brand{font-weight:700;color:var(--green);display:flex;align-items:center;gap:6px}
.brand .dot{width:22px;height:22px;border-radius:50%;background:var(--green)}
.photo{position:relative;overflow:hidden}
.badge{position:absolute;top:12px;height:34px;background:#dfe6ef;border-radius:2px}
.nav{left:106px;top:60px;width:988px;height:74px;background:var(--white)}
.nav ul{position:absolute;left:268px;top:20px;display:flex;list-style:none;font-size:12.5px}
.nav li{padding:8px 12px;margin-right:2px}
.nav li.active{background:var(--green);color:var(--white);border-radius:2px}
.hero{left:106px;top:134px;width:988px;height:438px;
  background:
    radial-gradient(ellipse 160px 200px at 250px 220px,rgba(255,255,255,.9),rgba(255,255,255,0)),
    radial-gradient(ellipse 120px 180px at 540px 230px,rgba(60,70,80,.45),rgba(60,70,80,0)),
    linear-gradient(90deg,#eef1f3 0%,#dfe4e8 35%,#aab4bc 55%,#d3d9de 75%,#8f9aa3 100%)}
.hero-box{left:739px;top:134px;width:275px;height:313px;background:var(--green);color:var(--white);padding:50px 50px 0 41px;font-size:24px;font-weight:300;line-height:30px}
.hero-box b{font-weight:700}
.card{position:absolute;top:750px;width:225px;height:412px;background:var(--white)}
.card .img{position:absolute;left:0;width:225px;height:263px}
.card .bar{position:absolute;left:0;width:225px;height:5px;background:var(--green)}
.card .txt{position:absolute;left:0;width:225px;text-align:center}
.card h3{color:var(--green);font-weight:600;font-size:14.5px;margin-bottom:6px}
.card p{font-size:10.5px;line-height:14px}
.card .btn{position:static;width:84px;height:34px;margin:13px auto 0}
.news{position:absolute;top:1463px;width:250px}
.news .img{height:150px}
.news h4{color:var(--green);font-weight:500;font-size:12px;margin:22px 2px 9px;line-height:16px}
.news p{font-size:9.5px;color:var(--muted);line-height:13px;margin:0 2px}
.about{left:0;top:2294px;width:1200px;height:563px;
  background:
    radial-gradient(ellipse 220px 300px at 900px 320px,rgba(150,210,100,.55),rgba(150,210,100,0)),
    repeating-linear-gradient(90deg,rgba(0,0,0,.0) 0 40px,rgba(0,0,0,.08) 40px 70px),
    linear-gradient(90deg,#3f8a1f 0%,#5da833 40%,#7cc24a 62%,#4e9a26 100%)}
.about-box{left:106px;top:2381px;width:600px;height:387px;background:var(--white);padding:40px 48px}
.about-box h2{color:var(--green);font-size:40px;font-weight:600;line-height:40px}
.about-box .lead{font-size:13px;line-height:15px;margin:6px 0 22px}
.about-box h3{color:var(--green);font-size:19px;font-weight:600;margin-bottom:12px}
.about-box p{font-size:10px;line-height:12px;color:#444;margin-bottom:10px}
.contact{left:0;top:2857px;width:1200px;height:249px;background:var(--white)}
.small{font-size:11px;color:#444;line-height:19px}
.social{left:543px;top:3035px;display:flex;gap:6px}
.social span{width:19px;height:19px;border-radius:50%;background:var(--green);display:flex;align-items:center;justify-content:center}
.footer{left:0;top:3106px;width:1200px;height:251px;background:var(--green);color:var(--white)}
.footer h3{position:absolute;font-size:20px;font-weight:600}
.footer ul{position:absolute;list-style:none;font-size:11px;line-height:19px}
.bottom{left:0;top:3357px;width:1200px;height:62px;background:var(--gray-bg);font-size:10px;color:#555;text-align:center;line-height:62px}
</style>
</head>
<body>

<div class="badge" style="left:572px;width:80px" role="img" aria-label="F&ouml;rderhinweis"></div>
<div class="badge" style="left:674px;width:120px" role="img" aria-label="F&ouml;rderhinweis"></div>
<div class="btn btn-fill" style="left:812px;top:13px;width:138px;height:33px;gap:6px">
  <svg width="13" height="13" viewBox="0 0 24 24" fill="none" stroke="#fff" stroke-width="2"><path d="M22 16.9v3a2 2 0 0 1-2.2 2 19.8 19.8 0 0 1-8.6-3.1 19.5 19.5 0 0 1-6-6A19.8 19.8 0 0 1 2.1 4.2 2 2 0 0 1 4.1 2h3a2 2 0 0 1 2 1.7c.1.9.4 1.8.7 2.7a2 2 0 0 1-.5 2.1L8 9.8a16 16 0 0 0 6 6l1.3-1.3a2 2 0 0 1 2.1-.5c.9.3 1.8.6 2.7.7a2 2 0 0 1 1.9 2z"/></svg>
  03412 / 480 - 0</div>
<div class="btn btn-line" style="left:962px;top:13px;width:132px;height:33px;gap:6px">
  <svg width="14" height="12" viewBox="0 0 24 20" fill="none" stroke="#6db33f" stroke-width="2"><rect x="1" y="1" width="22" height="18" rx="2"/><path d="M1 3l11 8 11-8"/></svg>
  info@kolmatech.de</div>

<div class="abs nav">
  <div class="brand abs" style="left:18px;top:24px;font-size:16px"><span class="dot"></span>KOLMATECH</div>
  <ul>
    <li class="active">Jobs &amp; Karriere</li><li>Palettiertechnik</li><li>Packertechnik</li><li>F&ouml;rdertechnik</li><li>Anlagen</li><li>Unternehmen</li><li>Aktuelles</li>
  </ul>
</div>
<div class="abs hero" role="img" aria-label="Mitarbeiter in Schutzkleidung bedient eine Edelstahlanlage"></div>
<div class="abs hero-box">Qualit&auml;t, die &uuml;berzeugt durch mehr als <b>155 Jahre Tradition</b>, Geschichte und Erfahrung.</div>

<div class="section-title" style="top:620px">Unsere Produkte</div>
<div class="section-sub" style="top:676px">Erfahren Sie mehr &uuml;ber unsere Produkte. W&auml;hlen Sie eine Kategorie:</div>

<div class="card" style="left:113px">
  <div class="img" style="top:0;background:radial-gradient(ellipse 40px 60px at 70px 170px,#2f8a3a,rgba(47,138,58,0)),linear-gradient(180deg,#b9c4c0 0%,#8fa296 40%,#dfe5e2 70%,#5f7f66 100%)" role="img" aria-label="Gr&uuml;ne Glasflaschen auf Transportband"></div>
  <div class="bar" style="top:263px"></div>
  <div class="txt" style="top:285px"><h3>Palettiertechnik</h3><p>KoPal<br>Unsere Palettierfamilie</p><div class="btn btn-fill">Mehr dazu</div></div>
</div>
<div class="card" style="left:362px">
  <div class="txt" style="top:18px"><h3>Packertechnik</h3><p>KoPac<br>unsere Flaschenpacker</p><div class="btn btn-fill">Mehr dazu</div></div>
  <div class="bar" style="top:144px"></div>
  <div class="img" style="top:149px;height:263px;background:linear-gradient(180deg,#c9cfd3 0%,#d9894a 25%,#6d7a80 50%,#1f3238 100%)" role="img" aria-label="Flaschenpacker mit Greifern"></div>
</div>
<div class="card" style="left:612px">
  <div class="img" style="top:0;background:radial-gradient(ellipse 50px 110px at 110px 150px,rgba(235,240,245,.9),rgba(235,240,245,0)),linear-gradient(180deg,#d9a06a 0%,#9aa4ab 40%,#6d7880 70%,#4d5b63 100%)" role="img" aria-label="Leere Glasflaschen in Abf&uuml;llanlage"></div>
  <div class="bar" style="top:263px"></div>
  <div class="txt" style="top:285px"><h3>F&ouml;rdertechnik</h3><p>KoTrans<br>Beh&auml;lter- und Gebindetransport</p><div class="btn btn-fill">Mehr dazu</div></div>
</div>
<div class="card" style="left:863px">
  <div class="txt" style="top:18px"><h3>Gebrauchtmaschinen</h3><p>KoPal<br>Unsere Palettierfamilie</p><div class="btn btn-fill">Mehr dazu</div></div>
  <div class="bar" style="top:144px"></div>
  <div class="img" style="top:149px;height:263px;background:radial-gradient(ellipse 70px 110px at 150px 120px,#dbe6f0,rgba(219,230,240,0)),linear-gradient(160deg,#9fc2e6,#5d8fc4 60%,#c7d9ea)" role="img" aria-label="Schaltschrank mit Bedienkn&ouml;pfen"></div>
</div>

<div class="btn btn-line" style="left:494px;top:1207px;width:211px;height:46px;font-size:15px">Alle Produkte anzeigen</div>

<div class="abs" style="left:0;top:1305px;width:1200px;height:538px;background:var(--white)"></div>
<div class="section-title" style="top:1352px">Aktuelles</div>
<div class="section-sub" style="top:1407px">Termine und aktuelle Meldungen</div>
<svg class="abs" style="left:106px;top:1530px" width="44" height="22" viewBox="0 0 44 22" fill="none" stroke="#6db33f" stroke-width="1.5"><path d="M43 11H2M11 2L2 11l9 9"/></svg>
<svg class="abs" style="left:1050px;top:1530px" width="44" height="22" viewBox="0 0 44 22" fill="none" stroke="#6db33f" stroke-width="1.5"><path d="M1 11h41M33 2l9 9-9 9"/></svg>
<div class="news" style="left:187px">
  <div class="img" style="background:linear-gradient(180deg,#b7bcbf 0%,#8e9396 25%,#b2642a 50%,#7a3f18 75%,#2e2a26 100%)" role="img" aria-label="Braune Flaschen auf F&ouml;rderband"></div>
  <h4>Neue Abf&uuml;llanlage f&uuml;r Brunnhof Limo</h4>
  <p>Der traditionsreiche Limonadenhersteller Brunnhof Limo aus der Oberlausitz investierte 2022/23 in eine neue Abf&uuml;llanlage.&hellip;</p>
</div>
<div class="news" style="left:475px">
  <div class="img" style="background:linear-gradient(180deg,#b9c4c0 0%,#8fa296 45%,#3c8a45 75%,#dfe5e2 100%)" role="img" aria-label="Gr&uuml;ne Flaschen in Glasabf&uuml;llanlage"></div>
  <h4>Erneuerung Glasabf&uuml;llanlage Molkereigenossenschaft Talheim</h4>
  <p>Die Molkereigenossenschaft Talheim erneuerte von 2020 bis 2022 in mehreren Bauabschnitten die Abf&uuml;llanlage f&uuml;r&hellip;</p>
</div>
<div class="news" style="left:763px">
  <div class="img" style="background:linear-gradient(90deg,#8d959c 0%,#d4d8dc 30%,#9aa2a9 55%,#cfd4d8 75%,#3c4248 100%)" role="img" aria-label="Edelstahltanks in Produktionshalle"></div>
  <h4>Neue Abf&uuml;llanlage f&uuml;r Brunnhof Limo</h4>
  <p>Der traditionsreiche Limonadenhersteller Brunnhof Limo aus der Oberlausitz investierte 2022/23 in eine neue Abf&uuml;llanlage.&hellip;</p>
</div>
<div class="btn btn-fill" style="left:531px;top:1738px;width:137px;height:46px;font-size:15px">Mehr lesen</div>

<div class="section-title" style="top:1890px">Jobs &amp; Karriere</div>
<div class="section-sub" style="top:1945px">Werden Sie Teil unseres Teams.</div>
<div class="abs" style="left:381px;top:1987px;width:437px;height:246px;background:radial-gradient(ellipse 200px 90px at 218px 190px,#3a5590,rgba(58,85,144,0)),linear-gradient(180deg,#7a6550 0%,#5a5448 40%,#3f4a5a 70%,#2a3242 100%)" role="img" aria-label="Videovorschau: drei Mitarbeiter in der Werkhalle"></div>
<svg class="abs" style="left:582px;top:2093px" width="34" height="34" viewBox="0 0 34 34"><circle cx="17" cy="17" r="17" fill="rgba(0,0,0,.55)"/><path d="M13 10l11 7-11 7z" fill="#fff"/></svg>
<div class="abs" style="left:381px;top:2219px;width:437px;height:14px;background:rgba(0,0,0,.7)"></div>
<div class="abs" style="left:400px;top:2225px;width:340px;height:2px;background:#888"></div>

<div class="abs about" role="img" aria-label="Mitarbeiter mit Haarnetz und Atemschutz an Edelstahlanlage, gr&uuml;n eingef&auml;rbt"></div>
<div class="abs about-box">
  <h2>&Uuml;ber uns</h2>
  <p class="lead">Qualit&auml;t, die &uuml;berzeugt durch mehr als 155 Jahre Tradition,<br>Geschichte und Erfahrung.</p>
  <h3>KOLMATECH Maschinenbau GmbH</h3>
  <p>Wir sind ein Unternehmen mit einer &uuml;ber einhundertj&auml;hrigen Geschichte. Gegr&uuml;ndet im Jahre 1862 als Metallwarenfirma, wird die Firma heute in der vierten Generation weitergef&uuml;hrt und mit viel pers&ouml;nlichem Engagement ausgebaut.</p>
  <p>Sowohl r&auml;umlich, inzwischen stehen f&uuml;r die Produktion mehr als 2.500 m&sup2; zur Verf&uuml;gung, als auch produktseitig haben wir gerade in den letzten Jahren viel investiert. Dadurch stehen unseren Kunden beste Voraussetzungen zur Verf&uuml;gung, um alle Problemstellungen optimal zu l&ouml;sen.</p>
  <p>Mit einer hohen Fertigungstiefe stellen wir F&ouml;rder- und Verpackungstechnik von der einzelnen Maschine bis zur kompletten Anlage her.</p>
  <p>Gerne nehmen wir Ihre Problemstellungen in einem pers&ouml;nlichen Gespr&auml;ch entgegen.</p>
  <p>Mehr &uuml;ber die KOLMATECH Maschinenbau GmbH erfahren sie hier.</p>
</div>

<div class="abs contact"></div>
<div class="abs" style="left:545px;top:2900px;color:var(--green);font-size:42px;font-weight:600">Kontakt</div>
<div class="brand abs" style="left:315px;top:2960px;font-size:18px"><span class="dot"></span>KOLMATECH</div>
<div class="abs small" style="left:545px;top:2961px">KOLMATECH Maschinenbau GmbH<br>Am Werkhof 12<br>04700 Talstadt</div>
<div class="abs small" style="left:770px;top:2961px">Telefon: 03412 / 480 - 0<br>Fax: 03412 / 480 - 14<br>E-Mail: info@kolmatech.de</div>
<div class="abs social" aria-label="Social-Media-Links">
  <span><svg width="10" height="10" viewBox="0 0 24 24" fill="none" stroke="#fff" stroke-width="2.5"><circle cx="18" cy="5" r="3"/><circle cx="6" cy="12" r="3"/><circle cx="18" cy="19" r="3"/><path d="M8.6 13.5l6.8 4M15.4 6.5l-6.8 4"/></svg></span>
  <span><svg width="10" height="10" viewBox="0 0 24 24" fill="none" stroke="#fff" stroke-width="2.5"><path d="M10 14a5 5 0 0 0 7 0l3-3a5 5 0 0 0-7-7l-1 1"/><path d="M14 10a5 5 0 0 0-7 0l-3 3a5 5 0 0 0 7 7l1-1"/></svg></span>
  <span><svg width="10" height="10" viewBox="0 0 24 20" fill="none" stroke="#fff" stroke-width="2.5"><rect x="1" y="1" width="22" height="18" rx="2"/><path d="M1 3l11 8 11-8"/></svg></span>
  <span><svg width="10" height="10" viewBox="0 0 24 24" fill="none" stroke="#fff" stroke-width="2.5"><path d="M21 12a8 8 0 0 1-8 8H4l2-3a8 8 0 1 1 15-5z"/></svg></span>
  <span><svg width="10" height="10" viewBox="0 0 24 24" fill="none" stroke="#fff" stroke-width="2.5"><circle cx="12" cy="12" r="10"/><path d="M2 12h20M12 2a15 15 0 0 1 0 20M12 2a15 15 0 0 0 0 20"/></svg></span>
</div>

<div class="abs footer">
  <h3 style="left:107px;top:60px">Quicklinks</h3>
  <ul style="left:107px;top:104px"><li>Startseite</li><li>Unternehmen</li><li>Downloads</li></ul>
  <ul style="left:257px;top:104px"><li>Medien-Center</li><li>Presse</li><li>Aktuelles</li></ul>
  <ul style="left:407px;top:104px"><li>Jobs &amp; Karriere</li><li>Kontakt</li></ul>
  <h3 style="left:613px;top:60px">Produkte</h3>
  <ul style="left:613px;top:104px"><li>Palettiertechnik</li><li>Packertechnik</li><li>F&ouml;rdertechnik</li></ul>
  <ul style="left:751px;top:104px"><li>Anlagen</li><li>Gebrauchtmaschinen</li></ul>
</div>
<div class="abs bottom">2024 &copy; KOLMATECH Maschinenbau GmbH | Datenschutz Impressum</div>

</body>
</html>
```